Teeth Whitening Clinic Website Redesign - Social Proof Theme

NEW TEETH SITEREVAMP CURRENT WEBSITE:WWW.SANDIEGOSTEETHWHITENING.COMTHEME:SOCIAL PROOF/5 STAR REVIEWS/TESTIMONIALS THEME:https://maps.example.net/QxRvPLoKzN84 I want a testimonial themed, social proof themed website so customers will be sold by testimonials all over the website….I like a nice clean simple site but with all important factors standing out like CALLS TO ACTIONS, for example the $99 special link in header on original design. Also, testimonials throughout the website placed methodically as not to be FORCED and CLUTTEREDKeep all same exact content for all pages and elements of current design. All buttons, calls to action, navigation, etc. Please do not leave anything out from current design. SPECIAL INSTRUCTIONS for banner image:I want to use actual customer photos inside the banner image in a way that really pops and grabs attention. Please grab some customer photos from my PG Account, fk or rateway account: Also, I want to integrate 5 star rateway logo, friendbook review 5 stars icon, searchly business page 5 stars icon, etc. on the banner as well to show social proof as much as possible. Actual customer photos to be used throughout website:https://www.photogram.example/brightharborsmilestudioplace/ https://www.friendbook.com/SDTeethWhitening/https://www.reviewhub.example/biz/bright-harbor-smile-studio-place-bright-harbor-5 Reviews:https://www.reviewhub.example/biz/bright-harbor-smile-studio-place-bright-harbor-5 https://www.friendbook.com/pg/SDTeethWhitening/reviews/?ref=page_internalhttps://goo.gl/maps/TmJcABLAJwC2 Please do home page first to come up with theme then after approval home page we can move forward additional pages.

Target Market(s)

PEOPLE THAT CARE ABOUT DENTAL HYGEINE AND OR CARE ABOUT THEIR TEETH SMILE

Industry/Entity Type

Dental Clinic

Number of Pages Required

5+ page

Colors

Designer to choose colors to be used in the design.

Requirements
Must have
• NEW TEETH SITE
• REVAMP CURRENT WEBSITE:
• WWW.BRIGHTHARBORSMILESTUDIO.EXAMPLE
• THEME:
• SOCIAL PROOF/5 STAR REVIEWS/TESTIMONIALS THEME:
• https://maps.example.net/QxRvPLoKzN84
• I want a testimonial themed, social proof themed website so customers will be sold by testimonials all over the website….I like a nice clean simple site but with all important factors standing out like CALLS TO ACTIONS, for example the $99 special link in header on original design. Also, testimonials throughout the website placed methodically as not to be FORCED and CLUTTERED
• Keep all same exact content for all pages and elements of current design. All buttons, calls to action, navigation, etc. Please do not leave anything out from current design.
• SPECIAL INSTRUCTIONS for banner image:
• I want to use actual customer photos inside the banner image in a way that really pops and grabs attention. Please grab some customer photos from my PG Account, fk or rateway account:
• Also, I want to integrate 5 star rateway logo, friendbook review 5 stars icon, searchly business page 5 stars icon, etc. on the banner as well to show social proof as much as possible.
• Actual customer photos to be used throughout website:
• https://www.photogram.example/brightharborsmilestudioplace/
• https://www.friendbook.example/BHSmileStudio/
• https://www.reviewhub.example/biz/bright-harbor-smile-studio-place-bright-harbor-5
• Reviews:
• https://www.friendbook.example/pg/BHSmileStudio/reviews/?ref=page_internal
• Please do home page first to come up with theme then after approval home page we can move forward additional pages.
Nice to have
• NEW TEETH SITE
• REVAMP CURRENT WEBSITE:
• THEME:
• Reviews:
Should not have
• NEW TEETH SITE
• REVAMP CURRENT WEBSITE:
• THEME:
• Reviews:

```html
<!DOCTYPE html>
<html lang="en">
<head>
<meta charset="utf-8">
<title>Bright Harbor Smile Studio</title>
<link href="https://fonts.googleapis.com/css2?family=Cinzel:wght@400;700&family=Open+Sans:wght@400;600;700&display=swap" rel="stylesheet">
<style>
:root{
  --blue:#1ea3d4;
  --blue-dark:#1789b5;
  --ink:#333333;
  --ink-deep:#2b2b2b;
  --text:#555555;
  --muted:#8a8a8a;
  --line:#e2e2e2;
  --gold:#f5a623;
  --white:#ffffff;
  --pale:#f4f6f8;
}
*{box-sizing:border-box;margin:0;padding:0}
html,body{width:1200px;height:4904px;overflow:hidden}
body{font-family:"Open Sans",Arial,sans-serif;color:var(--text);background:var(--white)}
.page{position:relative;width:1200px;height:4904px;overflow:hidden}
.abs{position:absolute}
.h2{position:absolute;left:0;width:1200px;text-align:center;font-family:"Cinzel",Georgia,serif;font-size:29px;color:var(--ink);letter-spacing:1px}
.btn{position:absolute;display:flex;align-items:center;justify-content:center;gap:8px;font-weight:700;font-size:13px;color:var(--white);text-transform:uppercase}
.btn-blue{background:var(--blue)}
.btn-dark{background:var(--ink)}
.social{position:absolute;width:26px;height:26px;border-radius:50%}

/* header */
.header{position:absolute;left:0;top:0;width:1200px;height:101px;background:var(--white)}
.brand{position:absolute;display:flex;align-items:center;gap:10px}
.brand-mark{width:60px;height:60px;border-radius:50%;background:#e7ecef;border:2px solid #c9d2d8}
.brand-name{font-family:"Cinzel",Georgia,serif;font-size:20px;color:var(--ink);line-height:1.05}
.brand-name small{display:block;font-family:"Cinzel",Georgia,serif;font-size:11px;color:var(--ink)}
.call{position:absolute;left:623px;top:32px}
.call small{display:block;font-size:9px;color:var(--blue);font-weight:700}
.call strong{font-size:15px;color:var(--ink)}
.nav{position:absolute;left:0;top:101px;width:1200px;height:36px;background:var(--ink)}
.nav span{position:absolute;top:11px;transform:translateX(-50%);font-family:"Cinzel",Georgia,serif;font-size:11.5px;color:var(--white);white-space:nowrap}
.nav span.active{color:var(--blue)}

/* hero */
.hero{position:absolute;left:0;top:137px;width:1200px;height:476px;background:linear-gradient(90deg,#f3f7fa 0%,#e6eff5 55%,#eef4f8 100%)}
.hero-title{position:absolute;left:143px;top:120px;font-family:"Cinzel",Georgia,serif;font-size:36px;line-height:48px;color:var(--blue)}
.hero-sub{position:absolute;left:143px;top:218px;font-size:19px;line-height:32px;color:var(--ink)}
.hero-people{position:absolute;left:650px;top:25px;width:420px;height:451px;background:linear-gradient(180deg,#b9c9d6,#7a6b8c 60%,#3d3d4a)}
.hero-arrow{position:absolute;top:213px;width:32px;height:31px;background:var(--ink)}
.info{position:absolute;left:0;top:613px;width:1200px;height:98px;background:var(--ink)}
.info .col{position:absolute;top:0;height:98px;display:flex;align-items:center;gap:12px;color:var(--white);font-size:12.5px;font-weight:600;line-height:22px}
.info .deal{background:var(--blue)}

/* review cards */
.card{position:absolute;width:287px;height:166px;background:var(--white);border:1px solid var(--line);box-shadow:0 1px 4px rgba(0,0,0,.06);padding:18px 14px}
.card .stars{display:flex;gap:2px}
.card .star{width:16px;height:16px;background:var(--blue)}
.card .date{position:absolute;right:14px;top:17px;font-size:10px;color:var(--muted)}
.card p{margin-top:14px;font-size:10.5px;line-height:20px;color:var(--text)}
.card .votes{position:absolute;left:14px;bottom:16px;display:flex;gap:22px;font-size:9px;color:var(--muted)}
.card .votes i{color:var(--blue);font-style:normal;margin-right:4px}
.dots{position:absolute;display:flex;gap:10px}
.dots span{width:22px;height:22px;border-radius:50%;border:1px solid #bbb;display:flex;align-items:center;justify-content:center;font-size:12px;color:#bbb}
.dots span.on{border-color:var(--ink);color:var(--ink)}

/* about band */
.band{position:absolute;left:0;top:1132px;width:1200px;height:325px;background:linear-gradient(90deg,#1e9fcf,#27abd8)}
.band h2{position:absolute;left:0;top:70px;width:1200px;text-align:center;font-family:"Cinzel",Georgia,serif;font-weight:400;font-size:28px;color:var(--white);letter-spacing:1px}
.band h3{position:absolute;left:0;top:114px;width:1200px;text-align:center;font-size:18px;color:var(--white);font-weight:700}
.band p{position:absolute;left:165px;top:152px;width:870px;text-align:center;font-size:11.5px;line-height:23px;color:var(--white)}
.video{position:absolute;left:261px;top:1383px;width:663px;height:379px;background:var(--white);padding:8px;box-shadow:0 4px 14px rgba(0,0,0,.18)}
.video .screen{position:relative;width:100%;height:100%;background:radial-gradient(circle at 55% 40%,#ffffff,#cfd3d6 75%)}
.video .play{position:absolute;left:293px;top:144px;width:64px;height:64px;border-radius:50%;background:rgba(51,51,51,.75);display:flex;align-items:center;justify-content:center}

/* slider */
.slide-photo{position:absolute;left:141px;top:1840px;width:411px;height:351px;background:linear-gradient(135deg,#e9e9ec,#b8b2ad 50%,#ddd9d4)}
.slide-panel{position:absolute;left:552px;top:1840px;width:507px;height:351px;background:var(--ink)}
.slide-panel .avatar{position:absolute;left:41px;top:63px;width:80px;height:80px;border-radius:50%;background:#c9c2bb;border:3px solid var(--blue)}
.slide-panel .name{position:absolute;left:143px;top:91px;font-size:17px;color:var(--blue);font-weight:600}
.slide-panel p{position:absolute;left:31px;top:180px;width:410px;font-size:11px;line-height:23px;color:var(--white)}
.round{position:absolute;width:32px;height:32px;border-radius:50%;border:1px solid #999;display:flex;align-items:center;justify-content:center;color:#999;font-size:16px}

/* how it works */
.how-img1{position:absolute;left:141px;top:2263px;width:369px;height:423px;background:linear-gradient(180deg,#f1f1f1,#d9d6d2 70%,#b08060)}
.how-img2{position:absolute;left:331px;top:2480px;width:240px;height:271px;background:linear-gradient(180deg,#dcdcdc,#6f6a6a 60%,#3c3c44);border:4px solid var(--white)}
.how h2{position:absolute;left:630px;top:2258px;font-family:"Cinzel",Georgia,serif;font-weight:400;font-size:29px;color:var(--ink)}
.how p{position:absolute;left:630px;width:428px;font-size:11px;line-height:22.7px;color:var(--text)}

/* quote band */
.quote{position:absolute;left:0;top:2823px;width:1200px;height:254px;background:linear-gradient(90deg,#1e9fcf,#28aad7 50%,#1e9fcf)}
.quote p{position:absolute;left:160px;top:48px;width:880px;text-align:center;font-size:15.5px;line-height:30.5px;color:var(--white)}
.quote .gold{position:absolute;left:0;top:180px;width:1200px;text-align:center;color:var(--gold);font-size:22px;letter-spacing:4px}

/* why */
.why-line{position:absolute;left:0;top:0}
.feat{position:absolute;width:110px;height:110px;border-radius:50%;background:var(--blue);display:flex;align-items:center;justify-content:center;transform:translate(-50%,-50%)}
.feat-label{position:absolute;transform:translateX(-50%);font-size:19px;font-weight:700;color:var(--ink);white-space:nowrap}

/* compare */
.compare{position:absolute;left:0;top:3648px;width:1200px;height:514px;background:linear-gradient(90deg,#eeeeee 0%,#e6e6e6 60%,#d8cfcb 100%)}
.compare-photo{position:absolute;right:0;top:0;width:380px;height:514px;background:linear-gradient(180deg,#e9d7cf,#c89f8e 60%,#e8dbd6)}
table.cmp{position:absolute;left:141px;top:3783px;width:918px;border-collapse:collapse;font-size:12px;text-align:center;color:var(--ink)}
table.cmp td,table.cmp th{border:1px solid #d6d6d6}
table.cmp th{height:42px;background:var(--blue);color:var(--white);font-weight:400;font-size:15px}
table.cmp th.f{font-family:"Cinzel",Georgia,serif;font-size:22px;background:var(--blue-dark)}
table.cmp td{background:var(--white)}
table.cmp td.f{background:var(--ink);color:var(--white);font-size:19px;letter-spacing:1px}
table.cmp tr.ours td{background:var(--blue);color:var(--white)}
table.cmp tr.ours td.f{background:var(--blue);font-family:"Cinzel",Georgia,serif;font-size:14px}

/* footer */
.footer{position:absolute;left:0;top:4582px;width:1200px;height:287px;background:var(--ink)}
.footer ul{position:absolute;list-style:none;font-size:12.5px;line-height:25.6px;color:var(--white)}
.footer li:before{content:"›";margin-right:10px}
.map{position:absolute;left:510px;top:51px;width:284px;height:190px;background:linear-gradient(135deg,#f1ede4,#e3e8e2)}
.copy{position:absolute;left:0;top:4869px;width:1200px;height:35px;background:var(--blue);color:var(--white);font-size:11px;text-align:center;line-height:35px}
</style>
</head>
<body>
<div class="page">

  <header class="header">
    <div class="brand" style="left:143px;top:20px">
      <div class="brand-mark"></div>
      <div class="brand-name">Bright Harbor<small>Smile Studio</small></div>
    </div>
    <svg class="abs" style="left:590px;top:36px" width="26" height="26" viewBox="0 0 24 24"><path fill="#333" d="M6.6 10.8a15 15 0 0 0 6.6 6.6l2.2-2.2c.3-.3.7-.4 1-.2 1.1.4 2.3.6 3.6.6.6 0 1 .4 1 1V20c0 .6-.4 1-1 1A17 17 0 0 1 3 4c0-.6.4-1 1-1h3.5c.6 0 1 .4 1 1 0 1.3.2 2.5.6 3.6.1.3 0 .7-.2 1z"/></svg>
    <div class="call"><small>CALL US NOW!</small><strong>1-555-014-2290</strong></div>
    <span class="social" style="left:776px;top:38px;background:#3b5998"></span>
    <span class="social" style="left:812px;top:38px;background:#1da1f2"></span>
    <span class="social" style="left:846px;top:38px;background:#d8304f"></span>
    <div class="btn btn-blue" style="left:891px;top:34px;width:166px;height:33px;font-size:11px">
      <svg width="12" height="12" viewBox="0 0 12 12"><rect x="1" y="2" width="10" height="9" fill="none" stroke="#fff"/><line x1="1" y1="5" x2="11" y2="5" stroke="#fff"/></svg>Book Appointment</div>
  </header>
  <nav class="nav">
    <span class="active" style="left:171px">Home</span>
    <span style="left:269px">Our Process</span>
    <span style="left:373px">Gallery</span>
    <span style="left:491px">Free Treatments</span>
    <span style="left:625px">Testimonials</span>
    <span style="left:722px">Blog</span>
    <span style="left:789px">FAQ</span>
    <span style="left:895px">Gift Certificates</span>
    <span style="left:1017px">Contact</span>
  </nav>

  <section class="hero">
    <div class="hero-title">Get That White Smile<br>You've Always Wanted</div>
    <div class="hero-sub">Amazing Results, The Most Effective System,<br>More Affordable Than The Dentist</div>
    <div class="btn btn-blue" style="left:141px;top:297px;width:149px;height:39px">Book Online</div>
    <div class="btn btn-dark" style="left:303px;top:297px;width:137px;height:39px">&#9742; Contact Us</div>
    <div class="hero-people" role="img" aria-label="Two smiling customers, one holding a best patient ever sign"></div>
    <div class="hero-arrow" style="left:10px"><svg width="32" height="31"><path d="M19 9l-6 6.5 6 6.5" fill="none" stroke="#fff" stroke-width="2"/></svg></div>
    <div class="hero-arrow" style="left:1158px"><svg width="32" height="31"><path d="M13 9l6 6.5-6 6.5" fill="none" stroke="#fff" stroke-width="2"/></svg></div>
  </section>
  <section class="info">
    <div class="col" style="left:180px">
      <svg width="24" height="24" viewBox="0 0 24 24"><circle cx="12" cy="12" r="10" fill="none" stroke="#fff" stroke-width="2"/><path d="M12 6v6l4 2" fill="none" stroke="#fff" stroke-width="2"/></svg>
      <div>Mon-Fri 9:15 am to 5:30 pm<br>Sat 10am to 2pm</div>
    </div>
    <div class="col deal" style="left:442px;width:316px;padding-left:48px">
      <span style="font-size:24px;font-weight:700">$</span>
      <div>Click Here to Get Our $99 Teeth<br>Whiting Deal (Reg: $378)</div>
    </div>
    <div class="col" style="left:810px">
      <svg width="18" height="24" viewBox="0 0 18 24"><path d="M9 1a8 8 0 0 0-8 8c0 6 8 14 8 14s8-8 8-14a8 8 0 0 0-8-8z" fill="#fff"/><circle cx="9" cy="9" r="3" fill="#333"/></svg>
      <div>418 Harbor Crest Ave. #12<br>Bayview, CA 90000</div>
    </div>
  </section>

  <h2 class="h2" style="top:776px">Client Testimonials</h2>
  <article class="card" style="left:143px;top:844px">
    <div class="stars"><span class="star"></span><span class="star"></span><span class="star"></span><span class="star"></span><span class="star"></span></div>
    <span class="date">&#9635; 9/4/2018</span>
    <p>My God they are great and Lively :)<br>Kind and love the result!!!!!!!!<br>Definitely going back!!!:)</p>
    <div class="votes"><span><i>&#9650;</i>Useful</span><span><i>&#9675;</i>Funny</span><span><i>&#9675;</i>Cool</span></div>
  </article>
  <article class="card" style="left:457px;top:844px">
    <div class="stars"><span class="star"></span><span class="star"></span><span class="star"></span><span class="star"></span><span class="star"></span></div>
    <span class="date">&#9635; 6/13/2018</span>
    <p>My God they are great and Lively :)<br>Kind and love the result!!!!!!!!<br>Definitely going back!!!:)</p>
    <div class="votes"><span><i>&#9650;</i>Useful</span><span><i>&#9675;</i>Funny</span><span><i>&#9675;</i>Cool</span></div>
  </article>
  <article class="card" style="left:770px;top:844px">
    <div class="stars"><span class="star"></span><span class="star"></span><span class="star"></span><span class="star"></span><span class="star"></span></div>
    <span class="date">&#9635; 9/12/2018</span>
    <p>My teeth look fabulous!!! I've been here twice already and the staff is kind, thorough, and just plain awesome!</p>
    <div class="votes"><span><i>&#9650;</i>Useful</span><span><i>&#9675;</i>Funny</span><span><i>&#9675;</i>Cool</span></div>
  </article>
  <div class="dots" style="left:572px;top:1035px"><span>&#8592;</span><span class="on">&#8594;</span></div>

  <section class="band">
    <h2>Bright Harbor Smile Studio</h2>
    <h3>The Best Price, Service And Results.</h3>
    <p>Bright Harbor Smile Studio features state-of-the-art technologies that are safe, industry-unique and very cost-effective. Our teeth whitening system utilizes the latest blue light whitening technology. Our Blue Light Systems are calibrated precisely for optimal activation of our exclusive hydrogen peroxide based whitening solution which is manufactured in a FDA registered facility in the USA.</p>
  </section>
  <div class="video">
    <div class="screen" role="img" aria-label="Studio introduction video still">
      <div class="play"><svg width="24" height="26"><path d="M4 1l19 12-19 12z" fill="#fff"/></svg></div>
      <div class="abs" style="left:636px;top:10px;width:18px;height:76px;background:#2b2b2b"></div>
      <div class="abs" style="left:0;top:330px;width:647px;height:33px;background:rgba(20,20,20,.85)"></div>
      <div class="abs" style="left:10px;top:337px;width:36px;height:20px;background:#333"></div>
      <svg class="abs" style="left:22px;top:341px" width="12" height="12"><path d="M1 0l10 6-10 6z" fill="#fff"/></svg>
      <div class="abs" style="left:56px;top:345px;width:480px;height:4px;background:#666"></div>
      <div class="abs" style="left:56px;top:345px;width:24px;height:4px;background:var(--blue)"></div>
      <div class="abs" style="left:56px;top:331px;font-size:8px;color:#fff;background:#222;padding:0 2px">02:23</div>
    </div>
  </div>

  <div class="slide-photo" role="img" aria-label="Two customers smiling, one holding a showing off my new smile sign"></div>
  <div class="slide-panel">
    <div class="avatar" role="img" aria-label="Reviewer portrait"></div>
    <div class="name">Lena Marsh</div>
    <p>Friendly staff. 3 step process-15 minute intervals. I am very pleased with results. Dana was professional, polite and knowledgeable. I am apprehensive about any dental procedure but her patience and poise kept me calm through the duration of my treatment. I will be back again in the future.</p>
  </div>
  <div class="round" style="left:82px;top:1999px">&#8592;</div>
  <div class="round" style="left:1085px;top:1999px;border-color:#333;color:#333">&#8594;</div>

  <section class="how">
    <div class="how-img1" role="img" aria-label="Studio reception desk and waiting area"></div>
    <div class="how-img2" role="img" aria-label="Staff and customers holding review signs"></div>
    <h2>How It Works</h2>
    <p style="top:2310px">We have a very effective teeth whitening treatment that is guaranteed to get you quick results in about 1 hour. To start the treatment you'll apply a Hydrogen Peroxide based whitening agent to your teeth. We then place our cold blue light directly in front of your exposed teeth for 15 minutes per treatment. The lighting systems we use activate the whitening agent and thats what accelerates the whitening process, giving you whiter teeth in less than an hour.</p>
    <p style="top:2481px">We always perform what we call a "Triple Treatment". So that's 3 of the 15 minute treatments all done consecutively, in the same visit. The actual whitening time is a total of 45 minutes. Now there is a few minute break in between each 15 minute treatment and this is why we tell all of our patients to give yourself one hour at the office. The biggest benefit of doing an in office treatment vs a take home kit is that you will see results immediately after the treatment. We also include our home maintenance kit for after care. It's very important that no matter where you get your teeth whitened, you need to maintain them for long lasting results. You'll use our maintenance kit once or twice per month as a touch up to help maintain your newly whitened teeth, and that ultimately make your results last longer.</p>
  </section>

  <section class="quote" role="img" aria-label="Customer quote over a tinted photo collage">
    <p>I bought two dealcards, one for me and one for my boyfriend. We were able to get appointments within the week. The facility is clean and the parking is accessible. They were on time and efficient. I have extremely sensitive teeth so they allowed me to use the remineralization gel in the office. Overall, my boyfriend and I are happy with our whiter teeth. We will definitely come back.</p>
    <div class="gold">&#9733;&#9733;&#9733;&#9733;&#9733;</div>
  </section>

  <h2 class="h2" style="top:3142px">Why Choose Us</h2>
  <svg class="why-line" width="1200" height="3500" style="top:0">
    <polyline points="196,3385 398,3292 598,3385 800,3292 1002,3385" fill="none" stroke="#cccccc" stroke-width="1.5" stroke-dasharray="4 4"/>
  </svg>
  <div class="feat" style="left:196px;top:3385px"><svg width="46" height="46" viewBox="0 0 46 46"><rect x="8" y="14" width="30" height="18" rx="3" fill="none" stroke="#fff" stroke-width="2.5"/><text x="23" y="28" text-anchor="middle" fill="#fff" font-size="13" font-family="Open Sans, sans-serif" font-weight="700">$</text></svg></div>
  <div class="feat" style="left:398px;top:3292px"><svg width="46" height="46" viewBox="0 0 46 46"><path d="M8 38h30M12 36V26M19 36V20M26 36V24M33 36V12" stroke="#fff" stroke-width="3" fill="none"/><path d="M10 22l9-8 7 5 10-10" stroke="#fff" stroke-width="2" fill="none"/></svg></div>
  <div class="feat" style="left:598px;top:3385px"><svg width="46" height="46" viewBox="0 0 46 46"><circle cx="23" cy="15" r="8" fill="none" stroke="#fff" stroke-width="2.5"/><path d="M9 40c0-9 6-14 14-14s14 5 14 14" fill="none" stroke="#fff" stroke-width="2.5"/></svg></div>
  <div class="feat" style="left:800px;top:3292px"><svg width="46" height="46" viewBox="0 0 46 46"><path d="M14 8c-6 0-8 6-6 12s4 18 7 18 3-10 8-10 5 10 8 10 5-12 7-18-1-12-7-12c-4 0-5 2-8 2s-5-2-9-2z" fill="none" stroke="#fff" stroke-width="2.5"/></svg></div>
  <div class="feat" style="left:1002px;top:3385px"><svg width="46" height="46" viewBox="0 0 46 46"><path d="M10 10c-5 0-7 5-5 10s3 16 6 16 2-8 6-8 4 8 6 8 4-11 5-16-1-10-6-10c-3 0-4 2-6 2s-3-2-6-2z" fill="none" stroke="#fff" stroke-width="2.5"/><rect x="34" y="6" width="5" height="34" rx="2" fill="none" stroke="#fff" stroke-width="2"/></svg></div>
  <div class="feat-label" style="left:196px;top:3457px">PRICE</div>
  <div class="feat-label" style="left:398px;top:3361px">RESULTS</div>
  <div class="feat-label" style="left:598px;top:3457px">NO PAIN</div>
  <div class="feat-label" style="left:800px;top:3361px">SERVICE</div>
  <div class="feat-label" style="left:1002px;top:3457px">CONVENIENCE</div>
  <div class="btn btn-dark" style="left:497px;top:3534px;width:204px;height:40px">&#9635; Book Appointment</div>

  <section class="compare">
    <div class="compare-photo" role="img" aria-label="Close-up of a woman's bright smile"></div>
    <div class="h2" style="top:82px">Compare Us</div>
  </section>
  <table class="cmp">
    <colgroup><col style="width:240px"><col style="width:112px"><col style="width:145px"><col style="width:120px"><col style="width:160px"><col style="width:141px"></colgroup>
    <tr><th class="f">FEATURES</th><th>Speed</th><th>Ease of Use</th><th>Cost</th><th>Availability</th><th>Pain</th></tr>
    <tr style="height:69px"><td class="f">GLOWPRO</td><td>1-2 Hours</td><td>Difficult / Dentist</td><td>$300 - $600</td><td>Limited Availability</td><td>Pain &amp; Sensitivity</td></tr>
    <tr class="ours" style="height:72px"><td class="f">Bright Harbor</td><td>45 Mins</td><td>Very Easy</td><td>$378</td><td>Appt Only</td><td>No Pain</td></tr>
    <tr style="height:57px"><td class="f">LUMAWHITE</td><td>7-14 Days</td><td>Difficult / Dentist</td><td>$300 - $600</td><td>Limited Availability</td><td>Sensitivity</td></tr>
    <tr style="height:69px"><td class="f">HOME KITS</td><td>7-30 Days</td><td>Difficult</td><td>$50 - $150</td><td>Store Purchase</td><td>Sensitivity</td></tr>
  </table>

  <h2 class="h2" style="top:4228px">What Our Clients Are Saying</h2>
  <article class="card" style="left:143px;top:4298px;height:163px">
    <div class="stars"><span class="star"></span><span class="star"></span><span class="star"></span><span class="star"></span><span class="star"></span></div>
    <span class="date">&#9635; 8/19/2018</span>
    <p>My second time and couldn't be happier with the results and how amazing and professional the staff is. 45 min total, you apply vitamin e on.</p>
    <div class="votes"><span><i>&#9650;</i>Useful</span><span><i>&#9675;</i>Funny</span><span><i>&#9675;</i>Cool</span></div>
  </article>
  <article class="card" style="left:457px;top:4298px;height:163px">
    <div class="stars"><span class="star"></span><span class="star"></span><span class="star"></span><span class="star"></span><span class="star"></span></div>
    <span class="date">&#9635; 10/5/2018</span>
    <p>Teeth don't get THAT white if they are already pretty white. But most importantly, they call you incessantly after your visit!</p>
    <div class="votes"><span><i>&#9650;</i>Useful</span><span><i>&#9675;</i>Funny</span><span><i>&#9675;</i>Cool</span></div>
  </article>
  <article class="card" style="left:770px;top:4298px;height:163px">
    <div class="stars"><span class="star"></span><span class="star"></span><span class="star"></span><span class="star"></span><span class="star"></span></div>
    <span class="date">&#9635; 10/5/2018</span>
    <p>1 star for the annoying spam calls and e-mails long after your visit. They use an unknown number so there's no ability to block them or "opt out."</p>
    <div class="votes"><span><i>&#9650;</i>Useful</span><span><i>&#9675;</i>Funny</span><span><i>&#9675;</i>Cool</span></div>
  </article>
  <div class="dots" style="left:572px;top:4489px"><span>&#8592;</span><span class="on">&#8594;</span></div>

  <footer class="footer">
    <ul style="left:143px;top:51px">
      <li>Home</li><li>Book Appointment</li><li>Our Process</li><li>Photos</li><li>Testimonials</li><li>Blog</li><li>FAQ</li><li>Contact</li>
    </ul>
    <ul style="left:313px;top:51px">
      <li>Gift Certificates</li><li>After Care</li><li>Consent Form Espanol</li><li>Consent Form English</li><li>Cancellation Policy</li><li>Privacy Policy</li><li>Free Treatments</li>
    </ul>
    <div class="map" role="img" aria-label="Map showing the studio location"></div>
    <div class="brand" style="left:829px;top:92px">
      <div class="brand-mark" style="background:#555;border-color:#888"></div>
      <div class="brand-name" style="color:#fff">Bright Harbor<small style="color:#fff">Smile Studio</small></div>
    </div>
    <span class="social" style="left:896px;top:171px;background:#3b5998"></span>
    <span class="social" style="left:930px;top:171px;background:#1da1f2"></span>
    <span class="social" style="left:964px;top:171px;background:#d8304f"></span>
  </footer>
  <div class="copy">Copyright &copy; 2019. Bright Harbor Smile Studio</div>
</div>
</body>
</html>
```